Business Card Design Project - del varosi group

dear Sirs

we need business card design for our group ( DEL Varosi Group ) , i have got the Logo design of our group from pixel harbor in previous , so all need details relating to our group i think available with you, as well as the the chosen logo design

we hope to provide us with business card logo that to be appropaite and satisfactory to us .

thanks

note : logo design of our group is attached .
Updates

Reason: please extend the deadline of my project for additional 15 days because i didn't received appropriate design for our gruop yet . kindly beaware that i have received 77 design till now , supossed to send me 200-250 design at least . thanks

Target Market(s)

contents

name : Kerem EL Nadiri

position : Operation Manager

Industry/Entity Type

Business

Requirements
Must have

• person name

group logo
Nice to have
• logo color matching with back background

```html
<!DOCTYPE html>
<html lang="en">
<head>
<meta charset="utf-8">
<title>DEL Varosi Group – Business Card</title>
<link rel="stylesheet" href="https://fonts.googleapis.com/css2?family=Cormorant+SC:wght@700&family=Open+Sans:ital,wght@0,400;0,600;0,700;1,400&display=swap">
<style>
  :root {
    --brand-blue: #0f5f92;
    --brand-blue-deep: #0b4d78;
    --brand-blue-light: #2f7fb0;
    --accent-gold: #c99a2e;
    --ink: #3a3a3a;
    --ink-soft: #6a6a6a;
    --rule: #c9c9c9;
    --paper: #ffffff;
    --backdrop: #e9ebee;
  }
  * { box-sizing: border-box; margin: 0; padding: 0; }
  html, body { width: 1200px; height: 900px; overflow: hidden; }
  body {
    background: var(--backdrop);
    font-family: "Open Sans", Arial, sans-serif;
    position: relative;
  }
  .card {
    position: absolute;
    top: 295px;
    width: 540px;
    height: 310px;
    border-radius: 18px;
    overflow: hidden;
    box-shadow: 0 6px 18px rgba(0,0,0,.18);
  }
  .card--front { left: 45px; background: var(--paper); }
  .card--back {
    left: 615px;
    background: linear-gradient(160deg, var(--brand-blue) 0%, var(--brand-blue-deep) 100%);
  }

  /* Wordmark */
  .wordmark {
    position: absolute;
    display: flex;
    align-items: center;
    gap: 8px;
    font-family: "Open Sans", Arial, sans-serif;
    font-weight: 700;
    letter-spacing: .5px;
    white-space: nowrap;
  }
  .wordmark__square { display: block; width: 14px; height: 14px; }
  .card--front .wordmark { left: 34px; top: 36px; font-size: 24px; color: var(--brand-blue); }
  .card--front .wordmark__square { background: var(--brand-blue); }
  .card--back .wordmark {
    left: 0; right: 0; top: 138px; justify-content: center;
    font-size: 30px; color: var(--paper);
  }
  .card--back .wordmark__square { background: var(--paper); width: 16px; height: 16px; }

  /* Person */
  .name-tab {
    position: absolute; left: 0; top: 148px;
    width: 8px; height: 42px; background: var(--brand-blue);
  }
  .person-name {
    position: absolute; left: 32px; top: 150px;
    font-family: "Cormorant SC", Georgia, serif;
    font-weight: 700; font-size: 23px; color: var(--brand-blue);
    letter-spacing: .5px;
  }
  .person-title {
    position: absolute; left: 60px; top: 180px;
    font-size: 14px; color: var(--ink-soft);
  }

  .rule {
    position: absolute; left: 18px; right: 20px; top: 222px;
    height: 1px; background: var(--rule);
  }

  /* Contacts */
  .contact {
    position: absolute; display: flex; align-items: center; gap: 8px;
    font-size: 13.5px; color: var(--ink);
  }
  .contact svg { width: 12px; height: 12px; fill: var(--brand-blue); flex: none; }
  .contact--phone  { left: 18px;  top: 230px; }
  .contact--email  { left: 18px;  top: 257px; }
  .contact--mobile { left: 186px; top: 230px; }
  .contact--fax    { left: 186px; top: 257px; }
  .contact-divider {
    position: absolute; left: 318px; top: 232px;
    width: 1px; height: 44px; background: var(--rule);
  }
  .address {
    position: absolute; left: 330px; top: 232px;
    font-size: 13.5px; font-weight: 600; line-height: 1.5; color: var(--ink);
  }

  /* Footer band */
  .footer-band {
    position: absolute; left: 0; right: 0; bottom: 0; height: 16px;
    background: var(--brand-blue);
  }
  .footer-tab {
    position: absolute; right: 0; bottom: 0; width: 180px; height: 24px;
    background: var(--accent-gold);
    clip-path: polygon(14px 0, 100% 0, 100% 100%, 0 100%);
  }
  .footer-url {
    position: absolute; right: 20px; bottom: 4px;
    font-size: 14px; color: var(--paper);
  }

  /* Back */
  .swoosh { position: absolute; inset: 0; width: 100%; height: 100%; }
  .back-url {
    position: absolute; right: 30px; bottom: 22px;
    font-size: 13px; color: var(--paper);
  }
</style>
</head>
<body>

<section class="card card--front" aria-label="Business card front">
  <div class="wordmark"><span class="wordmark__square"></span>DEL VAROSI GROUP</div>

  <span class="name-tab"></span>
  <h1 class="person-name">Kerem EL Nadiri</h1>
  <p class="person-title">Operation Manager</p>

  <span class="rule"></span>

  <p class="contact contact--phone">
    <svg viewBox="0 0 24 24"><path d="M6.6 10.8a15.2 15.2 0 0 0 6.6 6.6l2.2-2.2c.3-.3.7-.4 1-.2 1.1.4 2.3.6 3.6.6.6 0 1 .4 1 1V20c0 .6-.4 1-1 1C10.6 21 3 13.4 3 4c0-.6.4-1 1-1h3.5c.6 0 1 .4 1 1 0 1.3.2 2.5.6 3.6.1.3 0 .7-.2 1z"/></svg>
    (123) 456-7890
  </p>
  <p class="contact contact--email">
    <svg viewBox="0 0 24 24"><path d="M2 5h20v14H2zm2 2v.5l8 5 8-5V7z"/></svg>
    info@delvarosi.com
  </p>
  <p class="contact contact--mobile">
    <svg viewBox="0 0 24 24"><path d="M7 1h10a2 2 0 0 1 2 2v18a2 2 0 0 1-2 2H7a2 2 0 0 1-2-2V3a2 2 0 0 1 2-2zm0 3v14h10V4z"/></svg>
    (123) 456-7890
  </p>
  <p class="contact contact--fax">
    <svg viewBox="0 0 24 24"><path d="M3 2h18v20H3zm3 3v5h12V5zm0 8v2h3v-2zm5 0v2h3v-2zm5 0v2h2v-2zM6 17v2h3v-2zm5 0v2h3v-2z"/></svg>
    (123) 456-7890
  </p>
  <span class="contact-divider"></span>
  <p class="address">P.O. Box: 40210,<br>Dubai United Arab Emirates</p>

  <span class="footer-band"></span>
  <span class="footer-tab"></span>
  <p class="footer-url">www.delvarosi.com</p>
</section>

<section class="card card--back" aria-label="Business card back">
  <svg class="swoosh" viewBox="0 0 540 310" preserveAspectRatio="none" aria-hidden="true">
    <path d="M-20 210 C 140 150, 330 70, 470 -20 L 530 -20 C 390 90, 190 190, -20 250 Z" fill="#ffffff" opacity=".12"/>
    <path d="M-20 120 C 90 90, 200 40, 280 -20 L 320 -20 C 230 60, 110 120, -20 150 Z" fill="#ffffff" opacity=".09"/>
    <path d="M150 330 C 300 240, 430 140, 560 40 L 560 90 C 450 180, 330 270, 220 330 Z" fill="#ffffff" opacity=".08"/>
  </svg>
  <div class="wordmark"><span class="wordmark__square"></span>DEL VAROSI GROUP</div>
  <p class="back-url">www.delvarosi.com</p>
</section>

</body>
</html>
```